Brindlewood Racquet Club app

Design a sporting app that can, post news, post events, capture and show live scores, link at least 6 websites, other functions would be an advantage. Real tennis is also known as Royal tennis and Court tennis.
This would be like a sporting clubs app that gives live scores.

Colors

Designer to choose colors to be used in the design.

Requirements
Must have
• post news, post events, capture and show live scores, link at least 6 websites,
Nice to have
• Instructions on how to launch the app on apple and android

```html
<!DOCTYPE html>
<html lang="en">
<head>
<meta charset="utf-8">
<title>Brindlewood Racquet Club – Events</title>
<link href="https://fonts.googleapis.com/css2?family=Source+Sans+3:wght@400;600;700&display=swap" rel="stylesheet">
<style>
  :root {
    --navy-deep: #08078a;
    --navy-mid: #1222b0;
    --blue-bright: #1d45d6;
    --ghost-text: #0b0f8e;
    --white: #ffffff;
    --card-shade: rgba(0, 0, 0, 0.92);
  }
  * { margin: 0; padding: 0; box-sizing: border-box; }
  html, body { width: 1200px; height: 2598px; overflow: hidden; }
  body {
    position: relative;
    font-family: "Source Sans 3", sans-serif;
    color: var(--white);
    background: linear-gradient(180deg, var(--navy-deep) 0%, var(--navy-mid) 45%, var(--blue-bright) 100%);
  }
  .backdrop { position: absolute; inset: 0; }
  .status-bar {
    position: absolute; top: 28px; left: 0; width: 100%; height: 36px;
  }
  .status-time {
    position: absolute; left: 107px; top: 0;
    font-size: 23px; font-weight: 600; letter-spacing: 0.5px;
  }
  .status-icons { position: absolute; right: 96px; top: 4px; }
  .page-heading {
    position: absolute; top: 150px; left: 0; width: 100%; height: 160px;
    text-align: center;
  }
  .heading-ghost {
    position: absolute; left: 0; right: 0; top: 0;
    font-size: 190px; font-weight: 700; line-height: 160px;
    color: var(--ghost-text); letter-spacing: 4px; opacity: 0.85;
  }
  .heading-title {
    position: absolute; left: 0; right: 0; top: 18px;
    font-size: 112px; font-weight: 700; line-height: 120px;
    letter-spacing: -1px;
  }
  .event-list { position: absolute; left: 34px; top: 358px; width: 1135px; }
  .event-card {
    position: relative; width: 100%; height: 392px;
    border-radius: 20px; overflow: hidden; margin-bottom: 51px;
    box-shadow: 0 6px 18px rgba(0, 0, 20, 0.35);
  }
  .event-photo { position: absolute; inset: 0; }
  .event-card::after {
    content: ""; position: absolute; inset: 0;
    background: linear-gradient(180deg, rgba(0,0,0,0) 40%, var(--card-shade) 100%);
  }
  .event-info { position: absolute; left: 44px; bottom: 40px; z-index: 1; }
  .event-date { font-size: 37px; font-weight: 700; line-height: 44px; }
  .event-summary { font-size: 28px; font-weight: 400; line-height: 40px; letter-spacing: 0.6px; }
  .photo-players { background: linear-gradient(120deg, #d9dde2 0%, #8a95a2 45%, #3b4252 100%); }
  .photo-serve { background: linear-gradient(160deg, #c9d8ea 0%, #5b7a3a 45%, #2e4a8c 100%); }
  .photo-ball { background: radial-gradient(circle at 62% 40%, #6d7a2a 0%, #2a3214 28%, #121410 60%); }
  .photo-toss { background: linear-gradient(135deg, #3a4535 0%, #4d5a40 45%, #c98a5f 75%, #2c3028 100%); }
  .photo-clay { background: linear-gradient(160deg, #b0603a 0%, #9a4f2e 55%, #5a2c18 100%); }
</style>
</head>
<body>
  <svg class="backdrop" width="1200" height="2598" viewBox="0 0 1200 2598" aria-hidden="true">
    <polygon points="860,0 1200,0 1200,260 600,200" fill="#0f1aa6" opacity="0.6"/>
    <polygon points="1200,1450 1200,2598 180,2598 560,2300" fill="#2350dc" opacity="0.35"/>
  </svg>

  <header class="status-bar">
    <span class="status-time">9:41</span>
    <svg class="status-icons" width="112" height="22" viewBox="0 0 112 22" aria-label="Signal, Wi-Fi and battery">
      <rect x="0" y="14" width="4" height="6" rx="1" fill="#fff"/>
      <rect x="6" y="10" width="4" height="10" rx="1" fill="#fff"/>
      <rect x="12" y="6" width="4" height="14" rx="1" fill="#fff"/>
      <rect x="18" y="2" width="4" height="18" rx="1" fill="#fff"/>
      <path d="M36 8 a16 16 0 0 1 22 0 l-2.4 2.6 a12.5 12.5 0 0 0 -17.2 0z M40 12.5 a10 10 0 0 1 14 0 l-2.5 2.6 a6.4 6.4 0 0 0 -9 0z M44.2 17 a4 4 0 0 1 5.6 0 L47 20z" fill="#fff"/>
      <rect x="70" y="2" width="36" height="18" rx="4" fill="none" stroke="#fff" stroke-width="2"/>
      <rect x="73" y="5" width="30" height="12" rx="2" fill="#fff"/>
      <rect x="108" y="8" width="3" height="6" rx="1" fill="#fff"/>
    </svg>
  </header>

  <div class="page-heading">
    <div class="heading-ghost" aria-hidden="true">EVENTS</div>
    <h1 class="heading-title">EVENTS</h1>
  </div>

  <main class="event-list">
    <article class="event-card">
      <div class="event-photo photo-players" role="img" aria-label="Player holding a tennis racquet at the net on a city court"></div>
      <div class="event-info">
        <h2 class="event-date">25 DECEMBER 2019</h2>
        <p class="event-summary">Lorem Ipsum is simply dummy text</p>
      </div>
    </article>
    <article class="event-card">
      <div class="event-photo photo-serve" role="img" aria-label="Player serving on an outdoor court beside blue stadium seating"></div>
      <div class="event-info">
        <h2 class="event-date">26 DECEMBER 2019</h2>
        <p class="event-summary">Lorem Ipsum is simply dummy text</p>
      </div>
    </article>
    <article class="event-card">
      <div class="event-photo photo-ball" role="img" aria-label="Close-up of a tennis ball on grass beneath the net"></div>
      <div class="event-info">
        <h2 class="event-date">27 DECEMBER 2019</h2>
        <p class="event-summary">Lorem Ipsum is simply dummy text</p>
      </div>
    </article>
    <article class="event-card">
      <div class="event-photo photo-toss" role="img" aria-label="Player in an orange visor tossing the ball to serve"></div>
      <div class="event-info">
        <h2 class="event-date">28 DECEMBER 2019</h2>
        <p class="event-summary">Lorem Ipsum is simply dummy text</p>
      </div>
    </article>
    <article class="event-card">
      <div class="event-photo photo-clay" role="img" aria-label="Tennis racquet and balls on a clay court"></div>
      <div class="event-info">
        <h2 class="event-date">30 DECEMBER 2019</h2>
        <p class="event-summary">Lorem Ipsum is simply dummy text</p>
      </div>
    </article>
  </main>
</body>
</html>
```